MRT Property - Business Cards

Looking for a business card & general letterhead, signage etc design for our new logo.

Colours:
000a20
0056a2
00b5ef
0088ce
68cef2

Fonts:
Poppins
Karla

Please keep look and feel of new brand - example in the zip package I sent.

```html
<!DOCTYPE html>
<html lang="en">
<head>
<meta charset="utf-8">
<title>MRT Property – Business Cards</title>
<link href="https://fonts.googleapis.com/css2?family=Poppins:wght@400;500;600;700&display=swap" rel="stylesheet">
<style>
  :root {
    --bg: #1b1c1f;
    --navy: #000a20;
    --card: #141a2b;
    --blue-deep: #0056a2;
    --blue-mid: #0088ce;
    --blue-bright: #00b5ef;
    --blue-light: #68cef2;
    --emboss: #2a3042;
    --white: #ffffff;
  }
  * { margin: 0; padding: 0; box-sizing: border-box; }
  html, body { width: 1200px; height: 852px; overflow: hidden; }
  body {
    background: var(--bg);
    font-family: "Poppins", sans-serif;
    display: flex;
    align-items: center;
    justify-content: center;
    gap: 60px;
  }
  .card {
    position: relative;
    width: 500px;
    height: 286px;
    border-radius: 18px;
    background: var(--card);
    overflow: hidden;
    box-shadow: 0 10px 30px rgba(0,0,0,.45);
  }
  .brand-name {
    font-weight: 700;
    line-height: 1;
    letter-spacing: 1px;
    white-space: nowrap;
  }
  /* front */
  .card-front .brand {
    position: absolute;
    left: 0; right: 0; top: 96px;
    text-align: center;
  }
  .card-front .brand-name { color: var(--emboss); font-size: 44px; }
  .card-front .web {
    position: absolute;
    left: 0; right: 0; bottom: 42px;
    text-align: center;
    font-size: 11px;
    letter-spacing: 6px;
    color: #8a93a8;
  }
  .card-front .base-band {
    position: absolute;
    left: 0; right: 0; bottom: 0;
    height: 14px;
    background: var(--blue-deep);
  }
  /* back */
  .card-back .waves { position: absolute; inset: 0; width: 100%; height: 100%; }
  .card-back .holder {
    position: absolute;
    right: 30px; top: 28px;
    text-align: right;
  }
  .holder-name {
    font-weight: 600;
    font-size: 20px;
    color: var(--blue-mid);
    line-height: 1.1;
  }
  .holder-role {
    font-size: 10px;
    color: var(--white);
  }
  .card-back .brand {
    position: absolute;
    left: 32px; top: 142px;
  }
  .card-back .brand-name { color: var(--blue-deep); font-size: 30px; }
  .contact {
    position: absolute;
    right: 24px; top: 138px;
    list-style: none;
    text-align: right;
    color: var(--white);
    font-size: 11px;
    line-height: 20px;
  }
  .contact li { display: flex; justify-content: flex-end; align-items: center; gap: 8px; }
  .contact svg { width: 11px; height: 11px; fill: var(--white); }
  .contact .spacer { width: 11px; }
</style>
</head>
<body>
  <section class="card card-front">
    <div class="brand"><span class="brand-name">MRT Property</span></div>
    <div class="web">www.mrtproperty.com</div>
    <div class="base-band"></div>
  </section>

  <section class="card card-back">
    <svg class="waves" viewBox="0 0 500 286" preserveAspectRatio="none">
      <path d="M500,80 C380,82 296,104 266,154 C236,206 146,242 0,250 L0,286 L500,286 Z" fill="var(--blue-bright)"/>
      <path d="M500,88 C380,90 298,112 268,162 C238,214 148,250 0,258 L0,286 L500,286 Z" fill="var(--navy)"/>
      <path d="M500,96 C380,98 300,120 270,170 C240,222 150,258 0,266 L0,286 L500,286 Z" fill="var(--blue-deep)"/>
    </svg>
    <div class="holder">
      <div class="holder-name">Callum Reid</div>
      <div class="holder-role">Associate Director</div>
    </div>
    <div class="brand"><span class="brand-name">MRT Property</span></div>
    <ul class="contact">
      <li>555-204-7316
        <svg viewBox="0 0 24 24"><path d="M6.6 10.8a15 15 0 0 0 6.6 6.6l2.2-2.2c.3-.3.7-.4 1-.2 1.1.4 2.3.6 3.6.6.6 0 1 .4 1 1V20c0 .6-.4 1-1 1A17 17 0 0 1 3 4c0-.6.4-1 1-1h3.5c.6 0 1 .4 1 1 0 1.3.2 2.5.6 3.6.1.3 0 .7-.2 1z"/></svg></li>
      <li>callum@mrtmail.com
        <svg viewBox="0 0 24 24"><path d="M2 5h20v14H2z M3 6l9 7 9-7" fill="none" stroke="#fff" stroke-width="2"/></svg></li>
      <li>www.mrtsample.com
        <svg viewBox="0 0 24 24"><circle cx="12" cy="12" r="9" fill="none" stroke="#fff" stroke-width="2"/><path d="M3 12h18M12 3c3 3 3 15 0 18M12 3c-3 3-3 15 0 18" fill="none" stroke="#fff" stroke-width="1.6"/></svg></li>
      <li>27 Harbour Vale Road Eastwood<span class="spacer"></span></li>
    </ul>
  </section>
</body>
</html>
```